Wordpress Theme for Cedarline Care

** Please view updated Sitemap2.pdf doc to clarify some confusion ***

This is a multiuser WordPress subscription site for Cedarline Care. Please see attachment for sitemap. Please do not include extra content like social media icons, search bars, or images. If you have questions, please ask for clarification.
The site contains the following pages and sub-pages:

1. Home
2. Our Clinic
2a. Our Clinic > Mission
2b. Our Clinic > Services
2c. Our Clinic > Clinic Policies
2d. Our Clinic > Schedules
3. Our Staff
3a. Our Staff > [Staff member page]
4. Resources
4a. Resources > Patient Health (index)
4b. Resources > Patient Health (index) > [post]
4c. Resources > Links
4d. Resources > Forms
5. Alerts
5a. Alerts > [Alert Page]
6. Contact Us

Includes the Following Pages, Subpages, and Content
1. Home
a. About Us
b. Our Staff
c. Bulletins
d. Accepting New Patients (shown as an alert widget)
e. Links
i. Physician Toolbox
ii. Book an Appointment
f. Clinic Policies
i. Show first 3 policies (e.g. Late Arrivals, Missed Appointments, Fees)
ii. Link to Clinic Policies page
g. Primary widget (displayed on all pages)
i. Hours of operation
ii. Contact Info
1. Tel
2. Fax
3. Email
4. Address
5. Get directions (link to Google Maps)
2. Our Clinic
a. Main Page
i. Clinic Name
ii. Overview
iii. Languages Spoken
iv. Secondary Navigation
1. Mission
2. Services
3. Clinic Policies
4. Schedules (see attachment)
b. Our Clinic > Mission
c. Our Clinic > Services
i. For each service include service TITLE and DESCRIPTION
d. Our Clinic > Clinic Policies
i. For each policy include policy TITLE and DESCRIPTION
ii. Include the following policies in mockup
1. Late arrivals
2. Missed appointments
3. Fees for missed appointments
4. Referrals and follow-ups
5. Services not covered by RDA
6. Information for LTF patients
7. Medical Legal Reports
e. Our Clinic > Schedules
3. Our Staff
a. Main Page
i. Display a list of staff members. Include NAME and DESIGNATION
b. Our Staff > [Staff Name]
i. Include NAME, PICTURE, DESIGNATION, and BIO
4. Resources
a. Resources > Patient Health
i. Main Page
1. Posts (ordered by date)
a. Title
b. Summary
2. Side Navigation
a. Post Categories
ii. Patient Health > [post title]
1. Title
2. Post Category
3. Date
4. Author
5. Summary
6. Body
b. Resources > Links
1. Secondary Navigation - Categories
a. Sample Categories:
i. Local Services
ii. RDA and Drug Coverage
iii. Mental Health Resources
2. Category page
a. Include the following links in the 'Local Services' category
i. Hypertension clinics
ii. Home Care services
iii. Vaccine Clinics
c. Resources > Forms
i. Display a table with form TITLE and CATEGORY
ii. Side Navigation
1. Form Categories
a. Use the following sample Categories
i. Referrals
ii. Insurance
iii. Intake
iv. Discharge
v. Waivers
5. Alerts
a. Main page
i. List of all Alert posts
1. Include post TITLE as a link to the post
ii. Side Navigation
1. Alerts Archive
a. shown as Month + Number of posts
iii. Alerts > [Alert page]
1. Include TITLE, DATE, AUTHOR, BODY
6. Contact Us
a. Map
b. Hours of operation
c. Address
d. Phone number
e. Fax number
e. Fax number
f. Map
g. Email

Design notes:
- fixed width
- responsive (need designs for mobile, tablet, and desktop)
- simple, dark font, white background
- use Font Awesome icons where needed
- user adds own logo

Target Market(s)

Cedarline Care

Industry/Entity Type

Medical

Number of Pages Required

5+ page

Font styles to use
Serif
Sans Serif

Requirements
Must have
• Please keep designs very simple.
• Examples:
• https://www.quolbin.com/install
• http://www.ventrohax.com/company/about-us
• http://brindlequota.org/
• http://www.trosk.com/
Should not have
• Minimal or no use of shadows and gradients

```html
<!DOCTYPE html>
<html lang="en">
<head>
<meta charset="utf-8">
<title>Our Staff – Cedarline Care</title>
<link href="https://fonts.googleapis.com/css2?family=Open+Sans:wght@400;600;700&display=swap" rel="stylesheet">
<style>
:root{
  --blue:#0a84d8;
  --topbar:#0b8ae0;
  --ink:#333333;
  --ink-soft:#555555;
  --line:#e3e3e3;
  --band:#f7f7f7;
  --photo:#f4f4f4;
  --footer:#2b2b2b;
  --footer-text:#8a8a8a;
  --footer-head:#a8a8a8;
}
*{box-sizing:border-box;margin:0;padding:0}
html,body{width:1200px;height:1148px;overflow:hidden}
body{font-family:"Open Sans",Arial,sans-serif;color:var(--ink);background:#fff;position:relative}
a{color:inherit;text-decoration:none}
.abs{position:absolute}

.topbar{left:0;top:0;width:1200px;height:30px;background:var(--topbar);color:#fff;font-size:10px}
.topbar .help{left:162px;top:9px}
.topbar .help span{border-left:1px solid #fff;padding-left:4px;margin-left:4px}
.topbar .links{right:161px;top:9px}
.topbar .links span{border-left:1px solid #fff;padding-left:6px;margin-left:6px}

.header{left:0;top:30px;width:1200px;height:83px}
.brand{left:162px;top:27px;display:flex;align-items:center;gap:10px;font-size:21px;font-weight:600;color:var(--ink)}
.brand .dot{width:14px;height:14px;border-radius:50%;background:var(--blue)}
.nav{right:161px;top:0;height:83px;display:flex;font-size:11px}
.nav a{display:flex;align-items:center;padding:0 20px;height:83px}
.nav a.active{background:var(--blue);color:#fff;padding:0 8px;margin:0 10px}
.nav a:last-child{padding-right:0}

.titleband{left:0;top:113px;width:1200px;height:59px;background:var(--band)}
.titleband h1{position:absolute;left:162px;top:15px;font-size:10px;font-weight:700}
.titleband p{position:absolute;left:162px;top:34px;font-size:10px}

.portrait{left:161px;top:210px;width:428px;height:300px;background:linear-gradient(180deg,#f7f7f7 0%,#eef0f2 60%,#e6eaee 100%);border-bottom:3px solid var(--blue)}

.profile{left:610px;top:206px;width:429px}
.profile h2{font-size:12.5px;font-weight:600;display:inline-block;padding:0 0 12px;border-bottom:2px solid var(--line);width:113px;white-space:nowrap}
.facts{margin-top:28px;font-size:9.5px}
.fact{display:flex;border-bottom:1px solid var(--line);padding:10px 0 12px}
.fact dt{width:88px;font-weight:700;flex:none}
.fact dd{color:var(--ink);line-height:15px;margin-top:-2px}
.fact:first-child{padding-top:0}
.timetable{display:inline-block;margin-top:12px;font-size:9.5px;color:var(--blue);text-decoration:underline}
.pager{display:flex;margin-top:32px}
.pager span{width:27px;height:27px;display:flex;align-items:center;justify-content:center}
.pager .prev{background:#f1f1f1}
.pager .next{background:var(--blue)}

.section-title{left:161px;top:544px;font-size:13px;font-weight:600;padding-bottom:9px;border-bottom:2px solid var(--line);width:90px}
.tabs{left:161px;top:594px;display:flex;gap:27px;font-size:11px}
.tabs a{padding-bottom:4px;border-bottom:1px solid #cfcfcf}
.tabs a.on{color:var(--blue);font-weight:600;border-color:var(--blue)}

.staff-card{top:637px;width:203px;height:241px}
.staff-card .photo{height:188px;background:linear-gradient(180deg,#f8f8f8 0%,#eef1f3 100%)}
.staff-card .caption{height:53px;border:1px solid #d6d6d6;padding:10px 7px}
.staff-card h3{font-size:12px;font-weight:600;color:var(--ink-soft)}
.staff-card p{font-size:10.5px;color:var(--blue);margin-top:3px}

.footer{left:0;top:922px;width:1200px;height:226px;background:var(--footer);border-top:4px solid var(--blue);color:var(--footer-text);font-size:9.5px}
.footer .fbrand{position:absolute;left:162px;top:43px;font-size:21px;font-weight:600;color:#fff;display:flex;align-items:center;gap:10px}
.footer .fbrand .dot{width:14px;height:14px;border-radius:50%;background:#fff}
.footer .about{position:absolute;left:162px;top:86px;width:205px;line-height:14px;color:#d8d8d8;font-size:9px}
.fcol{position:absolute;top:34px}
.fcol h4{font-size:12px;font-weight:600;color:var(--footer-head);margin-bottom:9px}
.fcol li{list-style:none;line-height:18px}
.fcol li.current{color:#cfcfcf}
.contact-grid{display:grid;grid-template-columns:89px auto;line-height:15px}
.footer .bottom{position:absolute;left:0;top:187px;width:1200px;border-top:1px solid #444;height:35px}
.footer .bottom span{position:absolute;top:12px}
</style>
</head>
<body>

<div class="abs topbar">
  <div class="abs help">To help Here : 555 010 2040<span>Email : hello@cedarline.example</span></div>
  <div class="abs links">Book an Appointment<span>Physician Toolbox</span></div>
</div>

<header class="abs header">
  <a class="abs brand" href="#"><span class="dot"></span>Cedarline Care</a>
  <nav class="abs nav">
    <a href="#">Home</a>
    <a href="#">Our Clinic</a>
    <a href="#">Newsletter</a>
    <a href="#" class="active">Our Staff</a>
    <a href="#">Resources</a>
    <a href="#">Contact Us</a>
  </nav>
</header>

<div class="abs titleband">
  <h1>OUR STAFF</h1>
  <p>HOME / OUR STAFF/STAFF-MEMBER</p>
</div>

<div class="abs portrait" role="img" aria-label="Portrait photo of the staff member in a white coat with a stethoscope"></div>

<section class="abs profile">
  <h2>Dr. Ellen Marsh</h2>
  <dl class="facts">
    <div class="fact"><dt>DESIGNATION :</dt><dd>PEDIATRIST</dd></div>
    <div class="fact"><dt>BIO :</dt><dd>Donec commodo oido. Nulla vitae elit libero, a pharetra augue. Mauris id Integer posuere erat ante dapibus posuere velit aliquet.</dd></div>
    <div class="fact"><dt>OFFICE :</dt><dd>367, HALL A</dd></div>
    <div class="fact"><dt>WORKING DAY :</dt><dd>MONDAY, THURSDAY, FRIDAY</dd></div>
  </dl>
  <a class="timetable" href="#">TIMETABLE</a>
  <svg width="12" height="8" viewBox="0 0 12 8" style="margin-left:6px;vertical-align:-1px"><path d="M0 4h10M7 1l3 3-3 3" stroke="#0a84d8" stroke-width="1.4" fill="none"/></svg>
  <div class="pager">
    <span class="prev"><svg width="6" height="8" viewBox="0 0 6 8"><path d="M4.5 1L1.5 4l3 3" stroke="#333" stroke-width="1.2" fill="none"/></svg></span>
    <span class="next"><svg width="6" height="8" viewBox="0 0 6 8"><path d="M1.5 1l3 3-3 3" stroke="#fff" stroke-width="1.2" fill="none"/></svg></span>
  </div>
</section>

<h2 class="abs section-title">OUR STAFF</h2>
<nav class="abs tabs">
  <a href="#" class="on">All Departments</a>
  <a href="#">Primary Health Care</a>
  <a href="#">Pediatric Clinic</a>
  <a href="#">Outpatient Surgery</a>
  <a href="#">Cardiac Clinic</a>
</nav>

<article class="abs staff-card" style="left:161px">
  <div class="photo" role="img" aria-label="Photo of Dr. Ellen Marsh"></div>
  <div class="caption"><h3>Dr. Ellen Marsh</h3><p>Pediatric Clinic</p></div>
</article>
<article class="abs staff-card" style="left:386px">
  <div class="photo" role="img" aria-label="Photo of Dr. Owen Pryce"></div>
  <div class="caption"><h3>Dr. Owen Pryce</h3><p>Cardiac Clinic</p></div>
</article>
<article class="abs staff-card" style="left:611px">
  <div class="photo" role="img" aria-label="Photo of Dr. Nina Calder"></div>
  <div class="caption"><h3>Dr. Nina Calder</h3><p>Rehabilitation Therapy</p></div>
</article>
<article class="abs staff-card" style="left:836px">
  <div class="photo" role="img" aria-label="Photo of Dr. Lucas Brenner"></div>
  <div class="caption"><h3>Dr. Lucas Brenner</h3><p>Laryngological Clinic</p></div>
</article>

<footer class="abs footer">
  <div class="fbrand"><span class="dot"></span>Cedarline Care</div>
  <p class="about">Lorem Ipsum is simply dummy text of the printing and typesetting industry. Lorem Ipsum has been the industry's standard dummy text</p>
  <div class="fcol" style="left:461px">
    <h4>Navigation</h4>
    <ul><li class="current">Home</li><li>Our Clinic</li><li>Newsletter</li><li>Our Staff</li><li>Resources</li></ul>
  </div>
  <div class="fcol" style="left:686px">
    <h4>Links</h4>
    <ul><li>Help</li><li>Support</li><li>Privacy Policy</li></ul>
  </div>
  <div class="fcol" style="left:836px">
    <h4>Contact Us</h4>
    <div class="contact-grid" style="margin-left:2px">
      <span>Telephone :</span><span>555-010-7788</span>
      <span>Email:</span><span>hello@cedarline.example</span>
      <span>Address:</span><span>48 Alder Row<br>Brookfield, Northland,<br>Z9X 4QP</span>
    </div>
  </div>
  <div class="bottom">
    <span style="left:162px">© 2015 Cedarline Care. All Rights Reserved</span>
    <span style="left:463px">About Us</span>
    <span style="left:530px">Terms of Use</span>
    <span style="left:615px">Privacy Policy</span>
  </div>
</footer>

</body>
</html>
```